Business Card Design - Photographer

I am a landscape photographer and I require a business card design. 

I require two designs:
1)  a double sided business card
 and
b)  a single sided business card 

The single sided design can either be the same as the double sided (with just one side having all the information)....or it can be an entire new design. Its up to you.

My corporate colours are (CMYK):

Blue   69, 32, 0, 0
Grey  72,  64,  47,  31
Green  32,  2,  91,  0
Yellow   0, 19, 92, 0
Orange  0, 39, 75, 0

Colour space in final file should be in CMYK.

The details that need to be included on the card:

- Use the provided Logo
- Name: Wiktor Baranowski
- Email:   sales@vistalumeworks.com.au
- Website:    vistalumeworks.com.au
- Twitter:    twitter.com/vistalumeworks
- Facebook:   facebook.com/vistalumeworks
- Mobile  0417 539 662

Please use the attached template to design the logo to the specified size, including the marked bleed lines. I have also attached my logo in PNG (transparent background) and ai format for you to use.

The final file should be:
- Photoshop version with layers so I can edit the name/text etc. All non vector files should be high resolution at 1039 x 697 pixels at 300 dpi.

I also require a file as:
- Vector based PDF

Anyway questions please contact me.

Thank you

Industry/Entity Type

Landscape

Logo styles of interest
Pictorial/Combination Logo
Abstract Logo
Wordmark Logo
Lettermark Logo
Requirements
Must have
• The details that need to be included on the card:

- Use the provided Logo
- Name: Wiktor Baranowski
- Email: sales@vistalumeworks.com.au
- Website: vistalumeworks.com.au
- Twitter: twitter.com/vistalumeworks
- Facebook: facebook.com/vistalumeworks
- Mobile 0417 539 662

```html
<!DOCTYPE html>
<html lang="en">
<head>
<meta charset="utf-8">
<title>Vistalume Works – Business Cards</title>
<link rel="stylesheet" href="https://fonts.googleapis.com/css2?family=Cinzel:wght@500&family=Arimo:wght@400;700&display=swap">
<style>
  :root {
    --backdrop: #ad8626;
    --card-white: #ffffff;
    --panel-grey: #ececed;
    --brand-grey: #3d3f4f;
    --brand-blue: #3d97d3;
    --brand-green: #a9c83a;
    --brand-yellow: #fcc817;
    --brand-orange: #f7a149;
    --ink: #222226;
    --night: #000000;
  }
  html, body {
    margin: 0;
    padding: 0;
    overflow: hidden;
  }
  .canvas {
    position: relative;
    width: 1200px;
    height: 686px;
    background: var(--backdrop);
    overflow: hidden;
  }
  .card {
    position: absolute;
    width: 462px;
    height: 263px;
    border-radius: 22px;
    overflow: hidden;
  }
  /* Front card */
  .card-front {
    left: 123px;
    top: 102px;
    background: var(--card-white);
  }
  .colour-strip {
    position: absolute;
    right: 0;
    top: 0;
    width: 21px;
    height: 100%;
    background: linear-gradient(to bottom, var(--brand-orange) 0%, var(--brand-yellow) 30%, var(--brand-green) 62%, var(--brand-blue) 90%);
  }
  .contact-panel {
    position: absolute;
    left: -20px;
    top: 150px;
    width: 483px;
    height: 160px;
    border-radius: 50% 50% 0 0 / 38px 38px 0 0;
    background: linear-gradient(to bottom, #f4f4f5, var(--panel-grey));
  }
  .brand-mark {
    position: absolute;
    left: 186px;
    top: 14px;
    width: 78px;
    height: 78px;
    border-radius: 50%;
    background: var(--brand-grey);
  }
  .brand-name {
    position: absolute;
    left: 0;
    width: 441px;
    top: 98px;
    margin: 0;
    text-align: center;
    font-family: "Cinzel", serif;
    font-weight: 500;
    font-size: 22px;
    line-height: 26px;
    letter-spacing: 0.5px;
    color: var(--brand-grey);
  }
  .brand-rule {
    position: absolute;
    left: 121px;
    width: 214px;
    top: 125px;
    height: 1px;
    background: var(--brand-grey);
  }
  .tagline {
    position: absolute;
    left: 0;
    width: 441px;
    top: 129px;
    margin: 0;
    text-align: center;
    font-family: "Cinzel", serif;
    font-size: 9.5px;
    line-height: 12px;
    letter-spacing: 1.2px;
    color: var(--brand-grey);
  }
  .contact-list {
    position: absolute;
    left: 0;
    width: 441px;
    top: 160px;
    font-family: "Arimo", sans-serif;
    font-size: 12px;
    line-height: 17px;
    color: var(--ink);
    text-align: center;
  }
  .person-name {
    margin: 0 0 2px;
    font-family: "Arimo", sans-serif;
    font-weight: 700;
    font-size: 12.5px;
    line-height: 17px;
    color: var(--brand-grey);
  }
  .contact-row {
    display: flex;
    justify-content: center;
    align-items: center;
    gap: 14px;
    height: 17px;
    margin-bottom: 1px;
  }
  .contact-item {
    display: inline-flex;
    align-items: center;
    gap: 3px;
  }
  .social-square {
    width: 13px;
    height: 13px;
    border-radius: 2px;
    display: inline-block;
  }
  .social-square.fb { background: #3b5998; }
  .social-square.tw { background: #5cb6e4; }
  .contact-icon {
    width: 11px;
    height: 11px;
    fill: var(--brand-blue);
  }
  .address { margin-bottom: 1px; }
  .website {
    font-weight: 700;
    font-size: 12.5px;
    color: var(--brand-orange);
  }
  .website .domain { color: var(--brand-blue); }
  /* Back card */
  .card-back {
    left: 605px;
    top: 371px;
    background: var(--night);
  }
  .gloss-floor {
    position: absolute;
    left: -10px;
    top: 181px;
    width: 483px;
    height: 120px;
    border-radius: 50% 50% 0 0 / 40px 40px 0 0;
    background: linear-gradient(to bottom, #5b5b5e 0%, #2a2a2c 30%, #0b0b0c 70%, #000 100%);
  }
  .back-mark {
    position: absolute;
    left: 169px;
    top: 38px;
    width: 140px;
    height: 140px;
    border-radius: 50%;
    background: var(--card-white);
  }
</style>
</head>
<body>
<main class="canvas">

  <section class="card card-front" aria-label="Business card front">
    <div class="contact-panel"></div>
    <div class="colour-strip"></div>
    <div class="brand-mark"></div>
    <h1 class="brand-name">Vistalume Works</h1>
    <div class="brand-rule"></div>
    <p class="tagline">FINE ART PHOTOGRAPHY</p>

    <div class="contact-list">
      <p class="person-name">Wiktor Baranowski</p>
      <div class="contact-row">
        <span class="contact-item"><span class="social-square fb"></span>@vistalumeworks</span>
        <span class="contact-item"><span class="social-square tw"></span>@vistalumeworks</span>
      </div>
      <div class="contact-row">
        <span class="contact-item">
          <svg class="contact-icon" viewBox="0 0 24 24" aria-hidden="true"><path d="M6.6 10.8a15.1 15.1 0 0 0 6.6 6.6l2.2-2.2c.3-.3.7-.4 1-.2 1.1.4 2.3.6 3.6.6.6 0 1 .4 1 1V20c0 .6-.4 1-1 1A17 17 0 0 1 3 4c0-.6.4-1 1-1h3.5c.6 0 1 .4 1 1 0 1.3.2 2.5.6 3.6.1.3 0 .7-.2 1z"/></svg>
          0417 539 662
        </span>
        <span class="contact-item">
          <svg class="contact-icon" viewBox="0 0 24 24" aria-hidden="true"><path d="M2 5h20v14H2z"/><path d="M2 5l10 8 10-8" fill="none" stroke="#fff" stroke-width="1.6"/></svg>
          sales@vistalumeworks.com.au
        </span>
      </div>
      <div class="address">Street name City, State, zip code</div>
      <div class="website">www.<span class="domain">vistalumeworks</span>.com.au</div>
    </div>
  </section>

  <section class="card card-back" aria-label="Business card back">
    <div class="gloss-floor"></div>
    <div class="back-mark"></div>
  </section>

</main>
</body>
</html>
```